Valdo Capital

We need a corporate style website design for a new company based in Shenzhen's Qianhai Special Economic Development Zone, China. We provide a range of financial services to large international investment companies. Typically these companies invest over 5 million RMB. The company is part of a group that consists of NorthKilns, ValdoTrusts and ValdoEquity. Our location and gateway into Qianhai Special Economic Zone is our core advantage. We would like to see designs that Do Not use purple and orange. The website design should be similar to other websites in this family but different enough to give it a unique style (See attached website links for reference). The final design should communicate financial safety and growth. This website will act partly as a business chamber with connections to the government so we would like it to be diplomatic in style.

www.northkilns.example
www.valdotrusts.example

*Nevegation Bar
Should including Homepage, Financial Product, Team, News.
Could refer to www.valdotrusts.example

*Contact Details

Miss Lan
Address:E 728, North Block, KMO Centre, East Sector, Shenzhen Bright Science Campus
Telephone: +86 0755 63920417
Cellphone: +86 13957280316

* Social Media
Should be grouped like:
1. Weibo QRcode+ Weibo
2. Facebook, Twitter, Linkedin.

Industry/Entity Type

Investment

```html
<!DOCTYPE html>
<html lang="en">
<head>
<meta charset="utf-8">
<title>Valdo Capital</title>
<link rel="stylesheet" href="https://fonts.googleapis.com/css2?family=Open+Sans:ital,wght@0,400;0,600;0,700;1,400&family=Noto+Serif+SC:wght@400&family=Cinzel:wght@400&display=swap">
<style>
:root{
  --ink:#231f20;
  --dark:#2a2a2a;
  --footer:#2e2e2e;
  --blue:#29a8e0;
  --card:#7aa6d9;
  --brown:#5b321a;
  --text:#555;
  --muted:#888;
  --line:#e1e1e1;
  --pale:#f4f4f4;
}
*{margin:0;padding:0;box-sizing:border-box}
html,body{width:1034px;height:1200px;overflow:hidden;background:#fff;font-family:"Open Sans",sans-serif;color:var(--text)}
.page{position:relative;width:1034px;height:1200px}
.abs{position:absolute}
/* top bar */
.topbar{left:0;top:0;width:1034px;height:16px;background:var(--ink);font-size:6.5px;font-weight:700;color:#ddd}
.topbar .links{position:absolute;left:209px;top:4px;display:flex;gap:14px}
.topbar .phone{position:absolute;left:740px;top:4px}
.topbar .login{position:absolute;left:798px;top:0;height:16px;width:34px;background:#3a3637;padding:4px 6px}
/* header */
.brand{left:202px;top:26px;display:flex;align-items:center;gap:8px}
.brand .mark{width:44px;height:44px;border-radius:50%;background:#1f6c8e}
.brand .name{font-family:"Cinzel",serif;font-size:19px;color:var(--ink);letter-spacing:.5px;line-height:1}
.brand .cn{font-family:"Noto Serif SC",serif;font-size:8.5px;color:#555;letter-spacing:1.4px;margin-top:3px}
.hcontact{left:711px;top:32px;font-size:8.5px;color:#333}
.hcontact .lang{color:#999;font-size:7px;margin-right:6px}
.socials{left:783px;top:52px;display:flex;gap:4px}
.socials span{width:14px;height:14px;border-radius:50%;background:#ddd}
/* nav */
.nav{left:202px;top:82px;width:631px;height:24px;background:var(--ink);display:flex;font-size:8.5px;color:#ddd}
.nav a{padding:6px 13px;border-right:1px solid #3a3637;text-decoration:none;color:#ddd}
.nav a.active{background:var(--blue);color:#fff}
.search{left:688px;top:84px;width:142px;height:20px;background:#fff;font-size:6.5px;font-style:italic;color:#aaa;padding:6px 8px}
.search svg{position:absolute;right:6px;top:4px}
/* slider */
.slider{left:202px;top:106px;width:631px;height:283px;background:linear-gradient(180deg,#6e8bb4 0%,#5a6f8f 30%,#3b3f4f 60%,#2e2a2a 100%);clip-path:polygon(0 0,100% 0,100% 82%,96% 100%,4% 100%,0 82%)}
.caption{left:246px;top:229px;width:222px;height:94px;background:rgba(20,20,20,.82);padding:6px 8px;color:#e8e8e8}
.caption h2{font-size:16px;font-weight:400;color:#fff;margin-bottom:5px}
.caption p{font-size:6.5px;line-height:10.8px}
.caption .more{font-size:7px;margin-top:4px;color:#fff}
.arrow{font-size:14px;color:#fff}
.dots{left:427px;top:370px;display:flex;gap:2px}
.dots span{width:44px;height:4px;background:#4a4a4a}
.dots span.on{background:var(--blue)}
/* tagline */
.tagline{left:202px;top:397px;width:631px;height:56px;background:var(--pale);border:1px solid var(--line);padding:19px 18px;font-size:13px;color:#333}
.tagline b{color:var(--brown);font-weight:700}
.tagline .hl{color:var(--blue)}
.cta{left:746px;top:411px;width:72px;height:28px;background:var(--blue);color:#fff;font-size:7px;text-align:center;line-height:28px}
/* service cards */
.card{top:467px;width:148px;height:109px;border:1px solid var(--line)}
.card .face{height:82px;background:var(--card);color:#fff;text-align:center;padding-top:16px;font-size:9.5px}
.card .face.brown{background:var(--brown)}
.card .face b{font-weight:700}
.card .face svg{display:block;margin:0 auto 10px}
.card .learn{font-size:7.5px;text-align:center;line-height:26px;color:#666}
/* section heads */
.shead{top:601px;height:29px;background:var(--dark);color:#fff;font-size:8px;font-weight:700;display:flex;align-items:center}
.shead .ico{width:34px;height:29px;background:var(--blue);position:relative;display:flex;align-items:center;justify-content:center;margin-right:13px}
.shead .ico::after{content:"";position:absolute;right:-5px;top:10px;border-left:5px solid var(--blue);border-top:5px solid transparent;border-bottom:5px solid transparent}
.pager{position:absolute;right:6px;top:6px;display:flex;gap:3px}
.pager span{width:17px;height:17px;background:#444;color:#ddd;font-size:9px;text-align:center;line-height:16px}
/* team */
.member{left:202px;width:201px;display:flex;gap:9px}
.member .photo{width:84px;height:61px;background:linear-gradient(135deg,#c9c4bd,#6d6a66);position:relative;flex:none}
.member .photo span{position:absolute;left:3px;bottom:4px;font-size:5px;color:#fff}
.member h4{font-size:8px;color:#333;line-height:10px;font-weight:700}
.member p{font-size:6.8px;line-height:10px;color:#777;margin-top:2px}
.member a{font-size:6.8px;color:#888}
/* clients */
.clients{left:416px;top:638px;width:201px;height:151px;border:1px solid var(--line);display:grid;grid-template-columns:1fr 1fr;grid-template-rows:repeat(3,1fr)}
.clients div{border-right:1px solid var(--line);border-bottom:1px solid var(--line);display:flex;align-items:center;justify-content:center;gap:4px;font-size:8px;font-weight:600;color:#35627f}
.clients i{width:10px;height:10px;border-radius:50%;background:#2d6ab0;display:block}
/* testimonial */
.quote{left:632px;top:638px;width:201px;height:117px;background:var(--pale);border:1px solid #d8d8d8;padding:9px 12px;font-size:8px;line-height:14px;font-style:italic;color:#777;font-family:Georgia,serif}
.quote::after{content:"";position:absolute;left:12px;bottom:-7px;border-top:7px solid #d8d8d8;border-right:7px solid transparent}
.author{left:632px;top:764px;font-family:Georgia,serif;font-style:italic;font-size:9px;color:#333}
.author small{display:block;font-size:6px;font-weight:700}
/* works */
.work{top:852px;width:148px;height:97px}
.work.overlay{background:#2c2729;color:#fff;padding:9px 12px}
.work.overlay h4{font-size:8.5px;line-height:11px}
.work.overlay p{font-size:6.8px;line-height:11px;color:#ddd;margin-top:2px}
/* footer */
.footer{left:0;top:969px;width:1034px;height:231px;background:var(--footer);color:#aaa}
.fh{top:984px;font-size:9px;color:var(--blue)}
.ftext{font-size:7px;line-height:11px;color:#aaa}
.field{background:#3b3b3b;border:1px solid #444;font-size:6px;color:#999;padding:5px 6px}
.btn{background:var(--blue);color:#fff;font-size:6px;font-weight:700;text-align:center}
.thumbs{left:362px;top:1007px;display:grid;grid-template-columns:repeat(4,33px);gap:5px}
.thumbs span{height:31px;background:linear-gradient(135deg,#d8cfc4,#7b6556)}
.thumbs span:nth-child(3n){background:linear-gradient(135deg,#eee,#a39b92)}
.thumbs span:nth-child(4n+1){background:linear-gradient(135deg,#f0e6de,#b44a2e)}
.info{left:525px;font-size:6.8px;color:#888;display:flex;gap:7px;align-items:center}
.rule{left:202px;top:1162px;width:631px;height:1px;background:#444}
.up{left:501px;top:1148px;width:28px;height:28px;border-radius:50%;border:2px solid #444;background:var(--footer)}
.copy{left:202px;top:1177px;font-size:6px;color:#aaa}
.fsocial{left:768px;top:1172px;display:flex;gap:6px}
.fsocial span{width:17px;height:17px;border-radius:3px;background:#444}
</style>
</head>
<body>
<div class="page">

  <div class="abs topbar">
    <div class="links"><span>About</span><span>Shortcodes</span><span>Sitemap</span><span>Contact</span></div>
    <div class="phone">(00) 4821 7730 516</div>
    <div class="login">Login</div>
  </div>

  <div class="abs brand">
    <div class="mark"></div>
    <div><div class="name">Valdo Capital</div><div class="cn">深圳前海瓦尔多资本有限公司</div></div>
  </div>
  <div class="abs hcontact"><span class="lang">EN | SP</span>
    <svg width="6" height="8" viewBox="0 0 6 8"><rect x=".5" y=".5" width="5" height="7" rx="1" fill="none" stroke="#333"/></svg>
    +86 0755 63920417</div>
  <div class="abs socials"><span></span><span></span><span></span></div>

  <nav class="abs nav">
    <a class="active">Home</a><a>Financial Products</a><a>Team</a><a>News</a>
  </nav>
  <div class="abs search">Search here...
    <svg width="12" height="12" viewBox="0 0 12 12"><circle cx="5" cy="5" r="3.5" fill="none" stroke="#bbb" stroke-width="1.2"/><line x1="7.6" y1="7.6" x2="11" y2="11" stroke="#bbb" stroke-width="1.4"/></svg>
  </div>

  <div class="abs slider" role="img" aria-label="Evening skyline of a city with lit office towers"></div>
  <div class="abs caption">
    <h2>Valdo Capital</h2>
    <p>Lorem ipsum dolor sit amet, consectetur adipisicing elit, sed do eiusmod tempor incididunt ut labore et dolore magna aliqua. Ut enim ad minim veniam, quis nostrud exercitation ullamco laboris nisi ut aliquip ex ea commodo consequat...</p>
    <div class="more">Read More »</div>
  </div>
  <div class="abs arrow" style="left:208px;top:364px">‹</div>
  <div class="abs arrow" style="left:817px;top:364px">›</div>
  <div class="abs dots"><span></span><span class="on"></span><span></span><span></span></div>

  <div class="abs tagline"><b>Valdo Capital</b> is Special Economic Development Zone &amp; <span class="hl">Finance Management</span></div>
  <div class="abs cta">Contact Us Now</div>

  <div class="abs card" style="left:201px"><div class="face brown">
    <svg width="26" height="28" viewBox="0 0 26 28" fill="#fff"><path d="M8 2l5 5 5-5-2 9h-6z"/><rect x="6" y="14" width="14" height="12" rx="3"/></svg>
    Investment <b>Funds</b></div><div class="learn">Learn more</div></div>
  <div class="abs card" style="left:362px"><div class="face">
    <svg width="28" height="28" viewBox="0 0 28 28" fill="none" stroke="#fff" stroke-width="2"><rect x="9" y="3" width="16" height="12"/><circle cx="6" cy="9" r="3" fill="#fff"/><path d="M3 26V14h6v12M17 15v10"/></svg>
    Finance <b>Consultancy</b></div><div class="learn">Learn more</div></div>
  <div class="abs card" style="left:524px"><div class="face">
    <svg width="30" height="28" viewBox="0 0 30 28" fill="none" stroke="#fff" stroke-width="2"><rect x="4" y="3" width="22" height="16"/><path d="M1 23h28"/><circle cx="15" cy="11" r="3"/></svg>
    Finance <b>Management</b></div><div class="learn">Learn more</div></div>
  <div class="abs card" style="left:685px"><div class="face">
    <svg width="28" height="28" viewBox="0 0 28 28" fill="none" stroke="#fff" stroke-width="2"><path d="M6 13L14 5l8 8M9 11v7h10v-7"/><path d="M3 22c6 0 8 3 14 3l8-4"/></svg>
    Real <b>Estate</b></div><div class="learn">Learn more</div></div>

  <div class="abs shead" style="left:202px;width:201px"><div class="ico">
    <svg width="14" height="12" viewBox="0 0 14 12" fill="none" stroke="#fff" stroke-width="1.3"><rect x="1" y="1" width="12" height="8"/><path d="M4 9v2l3-2"/></svg></div>OUR TEAM</div>
  <div class="abs shead" style="left:416px;width:201px"><div class="ico">
    <svg width="14" height="12" viewBox="0 0 14 12" fill="none" stroke="#fff" stroke-width="1.3"><rect x="1" y="2" width="12" height="9"/><circle cx="7" cy="6" r="2"/></svg></div>OUR CLIENTS</div>
  <div class="abs shead" style="left:632px;width:201px"><div class="ico">
    <svg width="14" height="13" viewBox="0 0 14 13" fill="#fff"><circle cx="6" cy="4" r="3"/><path d="M1 13c0-4 2-5 5-5s5 1 5 5z"/></svg></div>CLIENT TESTIMONIALS
    <div class="pager"><span>‹</span><span>›</span></div></div>

  <div class="abs member" style="top:638px">
    <div class="photo" role="img" aria-label="Portrait of the chief executive"><span>Wei Tan, CEO</span></div>
    <div><h4>Lorem Ipsum Dolor Sit Amet Consetutuer</h4><p>Lorem quis bibendum auctor, nisi elit consequat ipsum, nec</p><a>Read more</a></div>
  </div>
  <div class="abs member" style="top:712px">
    <div class="photo" role="img" aria-label="Portrait of a staff member"><span>Lin Shu, Employee</span></div>
    <div><h4>Lorem Ipsum Dolor Sit Amet Consetutuer</h4><p>Lorem quis bibendum auctor, nisi elit consequat ipsum, nec</p><a>Read more</a></div>
  </div>

  <div class="abs clients">
    <div>ValdoTrusts</div><div>NorthKilns</div>
    <div>Ardent Fund Guild</div><div><i></i>Haiwen</div>
    <div>Lumera</div><div><i></i>Keston</div>
  </div>

  <div class="abs quote">Aenean sollicitudin, lorem quis bibendum auctor, nisi elit consequat ipsum, nec sagittis sem nibh id elit. Duis sed odio sit amet nibh vulputate cursus a sit amet mauris. Morbi accumsan ipsum velit. Nam nec tellus a odio tincidunt auctor a ornare odio. Sed non mauris vitae erat consequat auctor eu in elit.</div>
  <div class="abs author">Daniel Reyes<small>C.E.O Company</small></div>

  <div class="abs shead" style="left:202px;top:815px;width:631px"><div class="ico">
    <svg width="14" height="12" viewBox="0 0 14 12" fill="none" stroke="#fff" stroke-width="1.3"><rect x="1" y="1" width="12" height="10"/><path d="M2 9l4-4 3 3 2-2 2 2"/></svg></div>RECENT WORKS
    <div class="pager"><span>‹</span><span>›</span></div></div>

  <div class="abs work" style="left:202px;background:linear-gradient(135deg,#e9edf1,#9aa4ad)" role="img" aria-label="Colleagues working at office desks"></div>
  <div class="abs work overlay" style="left:363px">
    <h4>Proin gravida nibh vel velit auctor</h4>
    <p>Lorem quis bibendum auctor, nisi elit consequat ipsum, nec sagittis sem nibh id elit. Duis sed odio sit</p>
    <svg class="abs" style="left:108px;top:80px" width="30" height="12" viewBox="0 0 30 12" fill="none" stroke="#fff" stroke-width="1.3"><circle cx="6" cy="5" r="4"/><path d="M9 8l3 3"/><rect x="19" y="2" width="9" height="9"/><path d="M23 7l6-6"/></svg>
  </div>
  <div class="abs work" style="left:524px;background:linear-gradient(135deg,#dfe4ea,#7d8794)" role="img" aria-label="Team meeting around a table"></div>
  <div class="abs work" style="left:686px;background:linear-gradient(135deg,#c9dbe9,#4b5663)" role="img" aria-label="Group of business people in an office"></div>

  <div class="abs footer"></div>
  <div class="abs fh" style="left:202px">Get our newsletter</div>
  <div class="abs fh" style="left:362px">Flickr Gallery</div>
  <div class="abs fh" style="left:525px">About us</div>
  <div class="abs fh" style="left:686px">Contact us</div>

  <div class="abs ftext" style="left:202px;top:1006px;width:150px">Velit auctor aliquet. Aenean sollicitudin, lorem quis bibendum auctor, nisi elit</div>
  <div class="abs field" style="left:202px;top:1036px;width:112px;height:18px">enter your e-mail address</div>
  <div class="abs btn" style="left:313px;top:1036px;width:34px;height:18px;line-height:18px">Sign Up!</div>

  <div class="abs thumbs" role="img" aria-label="Gallery of interior photographs">
    <span></span><span></span><span></span><span></span><span></span><span></span><span></span><span></span><span></span><span></span><span></span><span></span>
  </div>

  <div class="abs ftext" style="left:525px;top:1006px;width:148px">Lorem ipsum dolor sit amet, consectetuer adipiscing elit, sed diam nonummy nibh euismod tincidunt ut laoreet dolore magna aliquam erat volutpat. Ut wisi enim ad</div>
  <div class="abs info" style="top:1058px"><svg width="9" height="8" viewBox="0 0 9 8" fill="#666"><path d="M4.5 0L9 4H8v4H1V4H0z"/></svg>lorem ipsum street</div>
  <div class="abs info" style="top:1074px"><svg width="8" height="8" viewBox="0 0 8 8" fill="#666"><path d="M1 0l2 2-1 1c1 2 2 3 3 3l1-1 2 2-1 1C3 8 0 5 0 1z"/></svg>+123 (456) 870 2214</div>
  <div class="abs info" style="top:1090px"><svg width="9" height="7" viewBox="0 0 9 7" fill="none" stroke="#666"><rect x=".5" y=".5" width="8" height="6"/><path d="M.5.5l4 3 4-3"/></svg><span style="color:#ddd;text-decoration:underline">info@valdo.example</span></div>

  <div class="abs field" style="left:686px;top:1009px;width:71px;height:18px">Name</div>
  <div class="abs field" style="left:762px;top:1009px;width:71px;height:18px">E-mail</div>
  <div class="abs field" style="left:686px;top:1032px;width:147px;height:44px">Message</div>
  <div class="abs btn" style="left:798px;top:1083px;width:35px;height:15px;line-height:15px">Send</div>

  <div class="abs rule"></div>
  <div class="abs up"><svg width="24" height="24" viewBox="0 0 24 24" fill="none" stroke="#777" stroke-width="1.5"><path d="M8 14l4-4 4 4"/></svg></div>
  <div class="abs copy">© 2014 Valdo Capital, All Rights Reserved</div>
  <div class="abs fsocial"><span></span><span></span><span></span></div>
</div>
</body>
</html>
```